New Innovative Counselling and psychotherapy Service needs Business Card design

Keep it simple and professional. On one side, just company name and logo (perhaps in all blue) and maybe a tag line.

On other side (all white) my name and Qualifications in centre

Industry/Entity Type

Health And Wellness

Contact Information for Business Card

Dara Whelby
Counsellor & Psychotherapist
BSc (Psychol.), BA, Dip. (Couns. & Psych.), PG.Cert (CBT), FGTrK, ONRE

I will also require Mobile no, Email and web site address of which I'll pass on to final designer.

Font styles to use
Sans Serif

Requirements
Must have
• My Logo Only and please use the colours in logo that is in it.
Should not have
• Any other images

```html
<!DOCTYPE html>
<html lang="en">
<head>
<meta charset="utf-8">
<title>Kindred Lane – Business Card</title>
<link href="https://fonts.googleapis.com/css2?family=Lato:wght@400;700&display=swap" rel="stylesheet">
<style>
  :root {
    --backdrop: #ecebe8;
    --card-white: #ffffff;
    --brand-blue: #3fb0ea;
    --brand-green: #93d35c;
    --ink: #3a3a3a;
    --ink-soft: #555555;
    --rule: #c9c9c9;
  }
  * { box-sizing: border-box; margin: 0; padding: 0; }
  html, body {
    width: 1200px; height: 844px; overflow: hidden;
    background: var(--backdrop);
    font-family: "Lato", sans-serif;
  }
  .stage {
    width: 1200px; height: 844px;
    display: flex; align-items: center; justify-content: center; gap: 60px;
  }
  .card {
    width: 520px; height: 300px;
    border-radius: 4px;
    box-shadow: 0 6px 22px rgba(0,0,0,.18);
    position: relative; overflow: hidden;
  }

  /* Front side */
  .card-front { background: var(--card-white); padding: 34px 40px 26px; color: var(--ink); }
  .brand {
    display: flex; align-items: center; justify-content: center; gap: 14px;
    margin-bottom: 26px;
  }
  .brand-dot { width: 40px; height: 40px; border-radius: 50%; background: var(--brand-blue); }
  .brand-name { font-size: 30px; font-weight: 400; color: var(--ink); letter-spacing: .3px; }
  .holder-name { font-size: 22px; font-weight: 700; line-height: 1.1; }
  .holder-name .first { color: var(--brand-blue); }
  .holder-name .last { color: var(--brand-green); }
  .holder-role { font-size: 13.5px; color: var(--ink-soft); margin-top: 2px; }
  .holder-quals { font-size: 12.5px; color: var(--ink-soft); margin-top: 2px; }
  .rule { border: 0; border-top: 1px solid var(--rule); margin: 10px 0; }
  .contact { font-size: 12.5px; color: var(--ink-soft); }
  .contact .label { color: var(--brand-blue); font-weight: 700; }
  .contact .web { color: var(--brand-blue); }
  .tagline { font-size: 12.5px; letter-spacing: .6px; text-transform: uppercase; color: var(--ink); }

  /* Back side */
  .card-back { background: var(--brand-green); }
  .back-blue { position: absolute; top: 0; right: 0; width: 150px; height: 100%; background: var(--brand-blue); }
  .back-mark {
    position: absolute; left: 50%; top: 50%; transform: translate(-50%, -50%);
    display: flex; flex-direction: column; align-items: center; gap: 16px;
  }
  .back-dot { width: 170px; height: 170px; border-radius: 50%; background: #f4f4f4; }
  .back-name { font-size: 26px; font-weight: 400; color: #ffffff; }
</style>
</head>
<body>
<main class="stage">
  <section class="card card-front" aria-label="Card front">
    <div class="brand">
      <span class="brand-dot"></span>
      <span class="brand-name">Kindred Lane</span>
    </div>
    <h1 class="holder-name"><span class="first">Dara</span> <span class="last">Whelby</span></h1>
    <p class="holder-role">Counsellor &amp; Psychotherapist</p>
    <p class="holder-quals">BSc (Psychol.), BA, Dip. (Couns. &amp; Psych.), PG.Cert (CBT), FGTrK, ONRE</p>
    <hr class="rule">
    <p class="contact"><span class="label">P:</span> 085 2290 417 | <span class="label">E:</span> info@kindredlane.com | <span class="web">www.kindredlane.com</span></p>
    <hr class="rule">
    <p class="tagline">Caring for your psychological well-being is our top priority</p>
  </section>

  <section class="card card-back" aria-label="Card back">
    <div class="back-blue"></div>
    <div class="back-mark">
      <span class="back-dot"></span>
      <span class="back-name">Kindred Lane</span>
    </div>
  </section>
</main>
</body>
</html>
```